Website for enterprise software start-up

We need a new Wordpress website. We are an early stage start-up focused on mobile video technology for cellular operators. The audience is strategy, marketing and customer acquisition execs from the operators.

The purpose of the site is to act as a sales brochure and capture leads. A demo app can be downloaded from the current site, want to put that behind a contact form.

Current website is at www.velmora.tv. Similar number of pages. Looking for a clean design template, with minimal customization. Blog will remain as is.

Want to be able to modify the copy via Wordpress. Reference designs I like: quandrix.com, briskfold7metrics.com

Target Market(s)

Mobile operators and MVNOs in the US and Asia Pacific regions

Industry/Entity Type

Business Software

Coding

Coded - Design and coding required

Number of Pages Required

4 page

Font styles to use
Sans Serif

Colors
f78f20

Requirements
Must have
• Form for downloading sample apps.
• Landing page with image, Product, Blog, About, Contact
• Team page

```html
<!DOCTYPE html>
<html lang="en">
<head>
<meta charset="utf-8">
<title>Velmora Media — High Quality Mobile Engagement</title>
<link rel="stylesheet" href="https://fonts.googleapis.com/css2?family=Questrial&family=Lato:wght@400;700&display=swap">
<style>
  :root {
    --brand-orange: #dc6f14;
    --ink: #2b2b2b;
    --white: #ffffff;
    --footer-bg: #2a2a2a;
    --social: #5b5f66;
    --badge-blue: #1a5fd0;
    --badge-light: #e6e8ea;
  }
  * { box-sizing: border-box; margin: 0; padding: 0; }
  html, body { width: 1200px; height: 653px; overflow: hidden; }
  body { font-family: "Lato", Arial, sans-serif; color: var(--white); background: var(--white); position: relative; }

  .site-header { position: absolute; left: 0; top: 0; width: 1200px; height: 68px; background: var(--white); }
  .brand { position: absolute; left: 82px; top: 11px; height: 48px; display: flex; align-items: center; gap: 10px; }
  .brand-square { width: 48px; height: 48px; background: var(--brand-orange); }
  .brand-name { font-family: "Lato", Arial, sans-serif; font-weight: 700; font-size: 38px; color: var(--ink); letter-spacing: -0.5px; }
  .menu-toggle { position: absolute; left: 1081px; top: 18px; width: 41px; height: 33px; border: 2px solid var(--brand-orange); border-radius: 4px; background: var(--white); }
  .menu-toggle span { position: absolute; left: 7px; width: 23px; height: 2px; background: var(--brand-orange); }
  .menu-toggle span:nth-child(1) { top: 9px; }
  .menu-toggle span:nth-child(2) { top: 14px; }
  .menu-toggle span:nth-child(3) { top: 19px; }

  .hero { position: absolute; left: 0; top: 68px; width: 1200px; height: 541px; overflow: hidden; }
  .hero-photo { position: absolute; inset: 0;
    background:
      radial-gradient(ellipse 260px 320px at 830px 250px, rgba(230,232,234,0.9), rgba(230,232,234,0) 70%),
      linear-gradient(180deg, #cdbfb4 0%, #9ea5a6 45%, #a9b1b2 75%, #8c9596 100%); }
  .hero-photo::after { content: ""; position: absolute; right: 0; top: 0; width: 420px; height: 200px;
    background: linear-gradient(90deg, rgba(40,38,44,0), rgba(40,38,44,0.75)); }

  .hero-title { position: absolute; left: 82px; top: 118px; font-family: "Questrial", "Century Gothic", sans-serif; font-size: 40px; font-weight: 400; letter-spacing: 0.3px; white-space: nowrap; }
  .hero-lead { position: absolute; left: 82px; top: 188px; width: 560px; font-size: 19.5px; line-height: 23px; }

  .store-button { position: absolute; top: 275px; height: 57px; background: var(--brand-orange); border-radius: 3px; display: flex; align-items: center; color: var(--white); }
  .store-button.app-depot { left: 82px; width: 200px; }
  .store-button.play-bazaar { left: 301px; width: 223px; }
  .store-icon { width: 63px; height: 57px; display: flex; align-items: center; justify-content: center; border-right: 1px solid rgba(255,255,255,0.85); }
  .store-text { flex: 1; text-align: center; line-height: 1.15; }
  .store-text small { display: block; font-size: 13px; }
  .store-text strong { display: block; font-size: 19px; font-weight: 400; }

  .partner-badge { position: absolute; left: 82px; top: 366px; width: 177px; height: 61px; border-radius: 5px; background: var(--badge-light); overflow: hidden; }
  .partner-badge::before { content: ""; position: absolute; left: 0; top: 0; width: 62px; height: 61px; background: var(--badge-blue); }

  .site-footer { position: absolute; left: 0; top: 609px; width: 1200px; height: 44px; background: var(--footer-bg); }
  .copyright { position: absolute; left: 81px; top: 14px; font-size: 13px; }
  .social-links { position: absolute; left: 984px; top: 17px; display: flex; gap: 9px; list-style: none; }
  .social-links li { width: 27px; height: 27px; border-radius: 50%; background: var(--social); margin-top: -4px; }
</style>
</head>
<body>
  <header class="site-header">
    <div class="brand"><span class="brand-square"></span><span class="brand-name">velmora</span></div>
    <button class="menu-toggle" aria-label="Open menu"><span></span><span></span><span></span></button>
  </header>

  <section class="hero">
    <div class="hero-photo" role="img" aria-label="Blurred seaside background with a hand holding a smartphone showing a wave crashing on a rock"></div>
    <h1 class="hero-title">High Quality Mobile Engagement</h1>
    <p class="hero-lead">We engage mobile audiences with the right video content at the perfect moment.</p>

    <a class="store-button app-depot">
      <span class="store-icon">
        <svg width="24" height="42" viewBox="0 0 24 42" aria-hidden="true">
          <rect x="1.5" y="1.5" width="21" height="39" rx="3" fill="none" stroke="#fff" stroke-width="2.5"/>
          <line x1="2" y1="7" x2="22" y2="7" stroke="#fff" stroke-width="2"/>
          <line x1="2" y1="33" x2="22" y2="33" stroke="#fff" stroke-width="2"/>
          <circle cx="12" cy="37" r="1.6" fill="#fff"/>
        </svg>
      </span>
      <span class="store-text"><small>Available On</small><strong>APP DEPOT</strong></span>
    </a>

    <a class="store-button play-bazaar">
      <span class="store-icon">
        <svg width="28" height="28" viewBox="0 0 28 28" aria-hidden="true"><rect x="2" y="2" width="24" height="24" rx="3" fill="#fff"/></svg>
      </span>
      <span class="store-text"><small>Robo App On</small><strong>PLAY BAZAAR</strong></span>
    </a>

    <div class="partner-badge" aria-label="Certified developer partner badge"></div>
  </section>

  <footer class="site-footer">
    <p class="copyright">Copyright © 2016 Velmora Media. All Rights Reserved.</p>
    <ul class="social-links">
      <li aria-label="Circlet"></li>
      <li aria-label="Chirpa"></li>
      <li aria-label="Plusgrid"></li>
      <li aria-label="Worklink"></li>
    </ul>
  </footer>
</body>
</html>
```